Gobal construction supply company needs new business card design

I need a business card design for my global supply company using an existing logo. i will be looking to print these on rounded corner cards with the black background version of my logo on the back. on the front white background, my logo again and my simple details.

```html
<!DOCTYPE html>
<html lang="en">
<head>
<meta charset="utf-8">
<title>Meridian Build Supply – Business Card</title>
<link rel="stylesheet" href="https://fonts.googleapis.com/css2?family=Roboto:wght@400;500;700&display=swap">
<style>
  :root {
    --stage: #3b3b3b;
    --card-white: #f4f4f4;
    --card-black: #1c1c1c;
    --ink: #111111;
    --ink-soft: #555555;
    --accent-red: #d90000;
    --paper-white: #f2f2f2;
  }
  * { box-sizing: border-box; margin: 0; padding: 0; }
  html, body {
    width: 1200px; height: 960px; overflow: hidden;
    background: var(--stage);
    font-family: "Roboto", Arial, sans-serif;
  }
  .canvas { position: relative; width: 1200px; height: 960px; }

  .card {
    position: absolute; width: 600px; height: 343px;
    border-radius: 22px; overflow: hidden;
  }

  /* Front */
  .card-front { left: 186px; top: 113px; background: var(--card-white); color: var(--ink); }
  .brand-name {
    position: absolute; left: 33px; top: 98px;
    font-weight: 700; font-size: 19px; letter-spacing: 0.2px; color: var(--ink);
    white-space: nowrap;
  }

  .person { position: absolute; left: 332px; top: 142px; }
  .person-name { font-weight: 500; font-size: 22px; line-height: 1; }
  .person-title { margin-top: 6px; font-weight: 500; font-size: 15px; color: var(--accent-red); }

  .contact-list {
    position: absolute; left: 334px; top: 195px; list-style: none;
    font-size: 14.5px; color: var(--ink-soft);
  }
  .contact-list li { display: flex; align-items: center; height: 19px; }
  .contact-list svg { width: 14px; height: 14px; margin-right: 8px; fill: var(--ink); flex: none; }

  .address {
    position: absolute; left: 33px; top: 234px;
    font-size: 14.5px; line-height: 19px; color: var(--ink-soft); font-style: normal;
  }

  .web-band {
    position: absolute; left: 30px; top: 287px; width: 539px; height: 26px;
    background: var(--card-black); color: var(--paper-white);
    display: flex; align-items: center; justify-content: flex-end; padding-right: 12px;
    font-size: 14.5px; letter-spacing: 0.6px;
  }

  /* Back */
  .card-back { left: 434px; top: 511px; background: var(--card-black); color: var(--paper-white); }
  .brand-back-mark {
    position: absolute; left: 34px; bottom: 30px;
    font-weight: 700; font-size: 72px; line-height: 1; letter-spacing: -1px;
    color: var(--paper-white); white-space: nowrap;
  }
  .back-name, .back-web {
    position: absolute; top: 61px; height: 240px;
    writing-mode: vertical-rl; display: flex; align-items: center; justify-content: center;
    white-space: nowrap;
  }
  .back-name { left: 541px; font-weight: 700; font-size: 17px; }
  .back-web { left: 503px; font-size: 15px; letter-spacing: 1.5px; }
</style>
</head>
<body>
<main class="canvas">

  <section class="card card-front" aria-label="Business card front">
    <span class="brand-name">MERIDIAN BUILD SUPPLY</span>

    <div class="person">
      <p class="person-name">DANIEL REYES</p>
      <p class="person-title">CEO/FOUNDER</p>
    </div>

    <ul class="contact-list">
      <li><svg viewBox="0 0 24 24" aria-hidden="true"><path d="M6.6 10.8a15.1 15.1 0 0 0 6.6 6.6l2.2-2.2a1 1 0 0 1 1-.25 11.4 11.4 0 0 0 3.6.57 1 1 0 0 1 1 1V20a1 1 0 0 1-1 1A17 17 0 0 1 3 4a1 1 0 0 1 1-1h3.5a1 1 0 0 1 1 1c0 1.25.2 2.45.57 3.6a1 1 0 0 1-.25 1z"/></svg>612 540 3817</li>
      <li><svg viewBox="0 0 24 24" aria-hidden="true"><path d="M7 1h10a2 2 0 0 1 2 2v18a2 2 0 0 1-2 2H7a2 2 0 0 1-2-2V3a2 2 0 0 1 2-2zm0 3v14h10V4zm5 15.2a1.1 1.1 0 1 0 0 2.2 1.1 1.1 0 0 0 0-2.2z"/></svg>745 219 6083</li>
      <li><svg viewBox="0 0 24 24" aria-hidden="true"><path d="M6 2h12v5H6zM3 8h18a2 2 0 0 1 2 2v7h-4v5H5v-5H1v-7a2 2 0 0 1 2-2zm4 8v4h10v-4z"/></svg>391 706 2458</li>
      <li><svg viewBox="0 0 24 24" aria-hidden="true"><path d="M2 5h20v14H2zm2 2v.5l8 5 8-5V7l-8 5z"/></svg>daniel@meridianbuild.com</li>
    </ul>

    <address class="address">4120 Harbor Ridge Road<br>Portland, Oregon 97204</address>

    <div class="web-band">www.meridianbuild.com</div>
  </section>

  <section class="card card-back" aria-label="Business card back">
    <span class="brand-back-mark">MERIDIAN</span>
    <span class="back-web">www.meridianbuild.com</span>
    <span class="back-name">MERIDIAN BUILD SUPPLY</span>
  </section>

</main>
</body>
</html>
```